Harborline Auto LLC

Car Dealer Customer Service
Address: 2874 Cresthaven Road, Fernbrook, OH 43911
web: www.harborlineautoxq.net
email: harborlineautoxq@mailnest.example
Phone: (931) 555-0148
Phone: (629) 555-0173

```html
<!DOCTYPE html>
<html lang="en">
<head>
<meta charset="utf-8">
<title>Harborline Auto LLC – Business Card</title>
<link rel="stylesheet" href="https://fonts.googleapis.com/css2?family=Poppins:ital,wght@0,300;0,400;0,700;1,300&display=swap">
<style>
  :root {
    --page-bg: #2c2c2e;
    --card-bg: #252527;
    --card-bg-light: #2d2d30;
    --brand-blue: #1f86c6;
    --brand-gold: #e3a93a;
    --text-light: #e6e6e8;
    --text-muted: #cfcfd3;
    --pattern-dark: #1c1c1e;
    --pattern-mid: #3a3a3d;
    --pattern-light: #6a6a6e;
  }
  * { box-sizing: border-box; margin: 0; padding: 0; }
  html, body {
    width: 1200px; height: 1138px; overflow: hidden;
    background: var(--page-bg);
    font-family: "Poppins", Arial, sans-serif;
  }
  .canvas { position: relative; width: 1200px; height: 1138px; }

  .card {
    position: absolute;
    border-radius: 14px;
    background: linear-gradient(135deg, var(--card-bg-light), var(--card-bg));
    overflow: hidden;
  }
  .card--front { left: 274px; top: 185px; width: 624px; height: 377px; }
  .card--back  { left: 276px; top: 606px; width: 618px; height: 376px; }

  /* Front */
  .front-pattern {
    position: absolute; left: 99px; top: 0; right: 0; bottom: 0;
    background: linear-gradient(100deg, var(--pattern-dark) 0%, var(--pattern-mid) 55%, var(--pattern-light) 100%);
  }
  .front-name {
    position: absolute; left: 56px; top: 187px;
    transform: translate(-50%, -50%) rotate(90deg);
    white-space: nowrap;
    font-weight: 700; font-size: 26px; letter-spacing: 0.5px;
    color: var(--brand-blue);
  }
  .front-mark {
    position: absolute; left: 102px; top: 132px;
    width: 106px; height: 106px; border-radius: 50%;
    background: var(--brand-gold);
  }

  /* Back – content laid out portrait, turned a quarter clockwise */
  .back-content {
    position: absolute; left: 618px; top: 0;
    width: 376px; height: 618px;
    transform-origin: 0 0;
    transform: rotate(90deg);
  }
  .back-mark {
    position: absolute; left: 112px; top: 60px;
    width: 150px; height: 150px; border-radius: 50%;
    background: var(--brand-gold);
  }
  .brand-name {
    position: absolute; left: 68px; top: 214px;
    font-weight: 700; font-size: 26px; line-height: 30px; letter-spacing: 0.5px;
    color: var(--brand-blue); white-space: nowrap;
  }
  .tagline {
    position: absolute; left: 68px; top: 294px;
    font-style: italic; font-weight: 300; font-size: 16px;
    color: var(--text-muted); white-space: nowrap;
  }
  .phones { position: absolute; left: 94px; top: 326px; list-style: none; }
  .phones li {
    display: flex; align-items: center; gap: 10px;
    font-weight: 700; font-size: 21px; line-height: 25px;
    color: var(--brand-blue); letter-spacing: 0.5px; white-space: nowrap;
  }
  .phones svg { width: 17px; height: 17px; fill: var(--brand-gold); flex: none; }

  .divider {
    position: absolute; left: 68px; top: 436px; width: 196px;
    display: flex; align-items: center; gap: 8px;
  }
  .divider .rule { flex: 1; height: 1.5px; background: var(--brand-blue); }
  .divider svg { width: 16px; height: 16px; flex: none; }

  .contact { position: absolute; left: 68px; top: 462px; list-style: none; }
  .contact li {
    font-weight: 300; font-size: 14.5px; line-height: 24px;
    color: var(--text-light); white-space: nowrap;
  }
  .contact .accent { color: var(--brand-blue); }
</style>
</head>
<body>
<main class="canvas">

  <section class="card card--front" aria-label="Card front">
    <div class="front-pattern" role="img" aria-label="Repeating embossed brand emblem pattern in dark grey tones"></div>
    <div class="front-mark" aria-hidden="true"></div>
    <h1 class="front-name">HARBORLINE AUTO</h1>
  </section>

  <section class="card card--back" aria-label="Card back">
    <div class="back-content">
      <div class="back-mark" aria-hidden="true"></div>
      <h2 class="brand-name">HARBORLINE AUTO</h2>
      <p class="tagline">Car Dealer Customer Service</p>
      <ul class="phones">
        <li><svg viewBox="0 0 24 24"><path d="M2 9.5C2 6 6.5 4 12 4s10 2 10 5.5V11h-5V8.8c-1.4-.6-3.1-.9-5-.9s-3.6.3-5 .9V11H2z"/><path d="M6 12.5 8 10h8l2 2.5 1.5 7.5h-15z"/><circle cx="12" cy="15.5" r="2.4" fill="#252527"/></svg>931-555-0148</li>
        <li><svg viewBox="0 0 24 24"><path d="M2 9.5C2 6 6.5 4 12 4s10 2 10 5.5V11h-5V8.8c-1.4-.6-3.1-.9-5-.9s-3.6.3-5 .9V11H2z"/><path d="M6 12.5 8 10h8l2 2.5 1.5 7.5h-15z"/><circle cx="12" cy="15.5" r="2.4" fill="#252527"/></svg>629-555-0173</li>
      </ul>
      <div class="divider" aria-hidden="true">
        <span class="rule"></span>
        <svg viewBox="0 0 24 24" fill="none" stroke="var(--brand-gold)" stroke-width="2"><circle cx="12" cy="12" r="9"/><path d="M3 12h18M12 3c3 3 3 15 0 18M12 3c-3 3-3 15 0 18"/></svg>
        <svg viewBox="0 0 24 24" fill="none" stroke="var(--brand-gold)" stroke-width="2"><rect x="3" y="5" width="18" height="14" rx="1"/><path d="M3 6l9 7 9-7"/></svg>
        <svg viewBox="0 0 24 24" fill="none" stroke="var(--brand-gold)" stroke-width="2"><circle cx="12" cy="12" r="9"/><path d="M12 17s-4-4-4-7a4 4 0 0 1 8 0c0 3-4 7-4 7z"/></svg>
        <span class="rule"></span>
      </div>
      <ul class="contact">
        <li>harborlineautoxq@mailnest.example</li>
        <li>www.<span class="accent">harborlineautoxq</span>.net</li>
        <li>2874 Cresthaven Road,</li>
        <li>Fernbrook, OH 43911</li>
      </ul>
    </div>
  </section>

</main>
</body>
</html>
```